Investment company needing business card

We are wanting a business card which looks sharp and easy on the eye. We are thinking of having a business card with the logo embossed on it, to really make it stand out. We will only have a small amount of information of the business card, person's name, position, email address and phone number

Contact Information for Business Card

Danielle Frost
Executive Assistant
+64 21 473 5162
danielf@harwickpartners.co.nz

Requirements
Must have
• Embossed logo
Should not have
• Not to be busy

```html
<!DOCTYPE html>
<html lang="en">
<head>
<meta charset="utf-8">
<title>Harwick Partners – Business Card</title>
<link rel="stylesheet" href="https://fonts.googleapis.com/css2?family=Open+Sans:wght@400;600;700&display=swap">
<style>
  :root {
    --brand-green: #22b573;
    --brand-grey: #666a6d;
    --text-grey: #6d7073;
    --card-white: #ffffff;
    --page-bg: #e9eaec;
    --silver-light: #f2f2f2;
    --silver-dark: #8e9194;
  }
  * { margin: 0; padding: 0; box-sizing: border-box; }
  html, body { width: 1200px; height: 900px; overflow: hidden; }
  body {
    background: var(--page-bg);
    font-family: "Open Sans", Arial, sans-serif;
    position: relative;
  }
  .card {
    position: absolute;
    width: 620px;
    height: 354px;
    background: var(--card-white);
    border-radius: 22px;
    overflow: hidden;
    box-shadow: 0 10px 30px rgba(0,0,0,0.18);
  }
  .card--front { left: 70px; top: 80px; }
  .card--back { left: 510px; top: 470px; }

  .card__wave { position: absolute; inset: 0; width: 100%; height: 100%; }

  .wordmark {
    position: absolute;
    display: flex;
    align-items: center;
    gap: 12px;
    white-space: nowrap;
  }
  .wordmark__square {
    width: 34px;
    height: 34px;
    background: var(--brand-grey);
    border-radius: 3px;
    flex: none;
  }
  .wordmark__name {
    color: var(--brand-green);
    font-weight: 700;
    font-size: 26px;
    letter-spacing: 2px;
    text-transform: uppercase;
    line-height: 1;
  }
  .card--front .wordmark { left: 40px; top: 62px; }
  .card--back .wordmark {
    left: 50%;
    top: 50%;
    transform: translate(-50%, -50%);
  }
  .card--back .wordmark__square { width: 44px; height: 44px; }
  .card--back .wordmark__name { font-size: 32px; }

  .person { position: absolute; left: 44px; top: 238px; }
  .person__name {
    color: var(--brand-green);
    font-weight: 700;
    font-size: 20px;
    text-transform: uppercase;
    letter-spacing: 0.3px;
  }
  .person__role {
    color: var(--text-grey);
    font-size: 17px;
    margin-top: 2px;
  }

  .contact {
    position: absolute;
    right: 24px;
    top: 228px;
    list-style: none;
    color: var(--card-white);
    font-size: 12.5px;
    text-align: right;
    white-space: nowrap;
  }
  .contact__item {
    display: flex;
    justify-content: flex-end;
    align-items: center;
    gap: 7px;
    line-height: 25px;
  }
  .contact__icon { width: 12px; height: 12px; flex: none; }
</style>
</head>
<body>

  <section class="card card--front" aria-label="Business card front">
    <svg class="card__wave" viewBox="0 0 620 354" preserveAspectRatio="none" aria-hidden="true">
      <defs>
        <linearGradient id="silverEdge" x1="0" y1="0" x2="0" y2="1">
          <stop offset="0" stop-color="var(--silver-light)"/>
          <stop offset="0.5" stop-color="var(--silver-dark)"/>
          <stop offset="1" stop-color="var(--silver-light)"/>
        </linearGradient>
      </defs>
      <path d="M480 0 C 533 110, 318 170, 288 354" fill="none" stroke="url(#silverEdge)" stroke-width="9"/>
      <path d="M492 0 C 545 110, 330 170, 300 354 L620 354 L620 0 Z" fill="var(--brand-green)"/>
    </svg>

    <div class="wordmark">
      <span class="wordmark__square"></span>
      <span class="wordmark__name">Harwick Partners</span>
    </div>

    <div class="person">
      <p class="person__name">Danielle Frost</p>
      <p class="person__role">Executive Assistant</p>
    </div>

    <ul class="contact">
      <li class="contact__item">+64 21 473 5162
        <svg class="contact__icon" viewBox="0 0 12 12" aria-hidden="true"><path d="M2 1h3l1 3-1.5 1a6 6 0 0 0 2.5 2.5L8 6l3 1v3a1 1 0 0 1-1 1A9 9 0 0 1 1 2a1 1 0 0 1 1-1z" fill="#fff"/></svg>
      </li>
      <li class="contact__item">danielf@harwickpartners.co.nz
        <svg class="contact__icon" viewBox="0 0 12 12" aria-hidden="true"><rect x="0.5" y="2.5" width="11" height="7" fill="#fff"/><path d="M0.5 2.5 6 6.5 11.5 2.5" fill="none" stroke="var(--brand-green)" stroke-width="1"/></svg>
      </li>
      <li class="contact__item">www.harwickpartners.co.nz
        <svg class="contact__icon" viewBox="0 0 12 12" aria-hidden="true"><circle cx="6" cy="6" r="5.2" fill="none" stroke="#fff" stroke-width="1.2"/><ellipse cx="6" cy="6" rx="2.2" ry="5.2" fill="none" stroke="#fff" stroke-width="1"/><path d="M1 6h10" stroke="#fff" stroke-width="1"/></svg>
      </li>
    </ul>
  </section>

  <section class="card card--back" aria-label="Business card back">
    <div class="wordmark">
      <span class="wordmark__square"></span>
      <span class="wordmark__name">Harwick Partners</span>
    </div>
  </section>

</body>
</html>
```